Business Card Design Project

- makeup artist business card

- original and creative

- Elegant design

- Feel free to come out with cool designs but stick to being elegant and attractive

- Design relates to makeup

- includes name, occupation, contact numbers, email, website

- regular size business card

- round corner card

- double sided

- on 1 side it should just have the website name in the center " moonveilstudio.net "

Industry/Entity Type

Business

Requirements
Must have
• Delia Marsh
Makeup Artist
USA: +1 (415)772-0461
Singapore: +65 82307915
deliamarsh@moonveilstudio.net
www.moonveilstudio.net
Should not have
• nothing cartoon looking.
Pictures of makeup being grab from the internet.. Examples: eyes or lips.

```html
<!DOCTYPE html>
<html lang="en">
<head>
<meta charset="utf-8">
<title>Delia Marsh – Makeup Artist Business Card</title>
<link rel="stylesheet" href="https://fonts.googleapis.com/css2?family=Arimo:wght@400;700&family=Tinos:wght@700&display=swap">
<style>
  :root {
    --canvas: #f4e6ea;
    --card: #ffffff;
    --plum: #7a2458;
    --pink: #c2418f;
    --band-light: #d36aa9;
    --band-dark: #8a1f63;
    --band-deep: #6e1550;
    --ink: #2a2a2a;
    --dot: #b8397f;
  }
  * { box-sizing: border-box; margin: 0; padding: 0; }
  html, body { width: 1200px; height: 951px; overflow: hidden; }
  body {
    background: var(--canvas);
    font-family: "Arimo", Arial, sans-serif;
    position: relative;
  }
  .card {
    position: absolute;
    left: 230px;
    width: 740px;
    height: 423px;
    background: var(--card);
    border-radius: 30px;
    overflow: hidden;
    box-shadow: 0 4px 14px rgba(90, 30, 60, 0.12);
  }
  .card--back { top: 40px; }
  .card--front { top: 488px; }

  /* back side */
  .website-line {
    position: absolute;
    top: 50%;
    left: 0;
    right: 0;
    transform: translateY(-50%);
    display: flex;
    align-items: center;
    justify-content: center;
    gap: 18px;
  }
  .dots { display: flex; align-items: center; gap: 9px; }
  .dots span { width: 5px; height: 5px; border-radius: 50%; background: var(--dot); }
  .dots span.big { width: 8px; height: 8px; }
  .website-line__text { font-size: 30px; color: var(--ink); letter-spacing: 0.2px; }
  .website-line__text em { font-style: normal; color: var(--pink); }

  /* front side */
  .front-band { position: absolute; inset: 0; }
  .brand-name {
    position: absolute;
    left: 52px;
    top: 36px;
    color: var(--plum);
    font-size: 58px;
    line-height: 58px;
    font-weight: 400;
  }
  .brand-name span { display: block; }
  .brand-name span:nth-child(2) { padding-left: 42px; }
  .contact {
    position: absolute;
    left: 46px;
    top: 268px;
    list-style: none;
    font-size: 18px;
    color: var(--ink);
    line-height: 26px;
  }
  .contact li { display: flex; align-items: center; gap: 10px; }
  .contact svg { width: 16px; height: 16px; flex: none; }
  .contact .web { color: var(--ink); }
  .contact .web em { font-style: normal; color: var(--pink); }
  .identity {
    position: absolute;
    right: 46px;
    bottom: 48px;
    width: 220px;
    text-align: center;
    color: #fff;
  }
  .identity__name { font-family: "Tinos", Georgia, serif; font-weight: 700; font-size: 27px; }
  .identity__role { font-size: 19px; margin-top: 4px; }
</style>
</head>
<body>

  <section class="card card--back" aria-label="Card back">
    <div class="website-line">
      <div class="dots"><span></span><span></span><span></span><span class="big"></span></div>
      <p class="website-line__text">www.<em>moonveilstudio</em>.net</p>
      <div class="dots"><span class="big"></span><span></span><span></span><span></span></div>
    </div>
  </section>

  <section class="card card--front" aria-label="Card front">
    <svg class="front-band" viewBox="0 0 740 423" preserveAspectRatio="none" aria-hidden="true">
      <defs>
        <linearGradient id="bandGradient" x1="0" y1="0" x2="1" y2="1">
          <stop offset="0" stop-color="var(--band-deep)"/>
          <stop offset="0.5" stop-color="var(--band-dark)"/>
          <stop offset="1" stop-color="var(--band-deep)"/>
        </linearGradient>
      </defs>
      <path d="M455,0 Q412,215 492,423 L740,423 L740,0 Z" fill="var(--band-light)"/>
      <path d="M478,0 Q436,215 514,423" fill="none" stroke="#ffffff" stroke-width="3" opacity="0.8"/>
      <path d="M492,0 Q452,215 530,423 L740,423 L740,0 Z" fill="url(#bandGradient)"/>
    </svg>

    <h1 class="brand-name"><span>moonveil</span><span>studio</span></h1>

    <ul class="contact">
      <li>
        <svg viewBox="0 0 16 16"><path d="M4 1.5 L6.5 4.5 L5 6.2 Q6.5 9.5 9.8 11 L11.5 9.5 L14.5 12 L12.8 14.3 Q6.5 14 2 7 Q1.8 3 4 1.5 Z" fill="var(--plum)"/></svg>
        USA: +1 (415)772-0461
      </li>
      <li>
        <svg viewBox="0 0 16 16"><path d="M4 1.5 L6.5 4.5 L5 6.2 Q6.5 9.5 9.8 11 L11.5 9.5 L14.5 12 L12.8 14.3 Q6.5 14 2 7 Q1.8 3 4 1.5 Z" fill="var(--plum)"/></svg>
        Singapore: +65 82307915
      </li>
      <li>
        <svg viewBox="0 0 16 16"><rect x="1" y="3" width="14" height="10" rx="1.5" fill="var(--plum)"/><path d="M1.5 3.8 L8 9 L14.5 3.8" fill="none" stroke="#fff" stroke-width="1.3"/></svg>
        deliamarsh@moonveilstudio.net
      </li>
      <li>
        <svg viewBox="0 0 16 16"><circle cx="8" cy="8" r="7" fill="var(--plum)"/></svg>
        <span class="web">www.<em>moonveilstudio</em>.net</span>
      </li>
    </ul>

    <div class="identity">
      <p class="identity__name">Delia Marsh</p>
      <p class="identity__role">Makeup Artist</p>
    </div>
  </section>

</body>
</html>
```